Velk Partners Building Business Cards

We need a business card that reflects our business as "Solar Experts" in San Diego. Browse our website www.velkpartners.example our License needs to be displayed as "CSLB# 3867140" our phone number is (619) 555-0187

Save thousands on your electric bills and increase the value of your home while helping to protect the environment. Our solar installation experts will help you design the system that's right for you, using only the highest quality equipment that will look great and give you ideal performance. Our goal is to make you energy independent, and get your electric bill to 0.

Paul Osterby
(619) 555-0187
paul@velkpartners.example

Target Market(s)

Home owners in san diego looking for solar

Industry/Entity Type

Solar Energy

Contact Information for Business Card

Paul Osterby
(619) 555-0187
paul@velkpartners.example

Font styles to use
Other font styles liked:
• Use our logo font

Requirements
Must have
• License needs to be displayed as "CSLB# 3867140" our phone number is (619) 555-0187
Nice to have
• Real images of rooftop home solar in san diego
Should not have
• our business address

```html
<!DOCTYPE html>
<html lang="en">
<head>
<meta charset="utf-8">
<title>Velk Partners Building – Business Cards</title>
<link rel="stylesheet" href="https://fonts.googleapis.com/css2?family=Open+Sans:wght@400;600;700;800&display=swap">
<style>
  :root {
    --navy: #1d3f80;
    --navy-deep: #17346b;
    --gold: #f5b324;
    --gold-soft: #fbd66e;
    --ink: #4a4a4a;
    --paper: #ffffff;
    --backdrop: #e8e9ec;
  }
  * { box-sizing: border-box; margin: 0; padding: 0; }
  html, body {
    width: 1200px;
    height: 950px;
    overflow: hidden;
    background: var(--backdrop);
    font-family: "Open Sans", Arial, sans-serif;
  }
  .sheet {
    position: relative;
    width: 1200px;
    height: 950px;
  }
  .card {
    position: absolute;
    top: 108px;
    width: 420px;
    height: 735px;
    border-radius: 6px;
    overflow: hidden;
    box-shadow: 0 10px 30px rgba(0,0,0,0.18);
  }

  /* Front */
  .card-front {
    left: 140px;
    background: var(--paper);
  }
  .front-logo {
    position: absolute;
    top: 56px;
    left: 0;
    right: 0;
    text-align: center;
    font-weight: 800;
    font-size: 31px;
    letter-spacing: -0.5px;
    color: var(--navy);
    line-height: 1;
  }
  .contact {
    position: absolute;
    top: 150px;
    left: 0;
    right: 0;
    text-align: center;
    color: var(--ink);
    font-size: 17px;
    line-height: 1.55;
  }
  .contact .name {
    font-weight: 700;
    font-size: 23px;
    color: var(--navy);
    line-height: 1.25;
  }
  .contact .role {
    font-size: 17px;
    color: var(--gold);
    margin-bottom: 8px;
  }
  .contact .label { font-weight: 700; color: var(--navy); }
  .emblem-area {
    position: absolute;
    left: 0;
    bottom: 0;
    width: 420px;
    height: 320px;
    display: block;
  }

  /* Back */
  .card-back {
    left: 640px;
    background: var(--navy);
  }
  .back-logo {
    position: absolute;
    top: 50%;
    left: 50%;
    transform: translate(-50%, -50%) rotate(90deg);
    white-space: nowrap;
    font-weight: 800;
    font-size: 42px;
    letter-spacing: -0.5px;
    color: var(--paper);
  }
  .back-web {
    position: absolute;
    top: 50%;
    left: 58px;
    transform: translate(-50%, -50%) rotate(90deg);
    white-space: nowrap;
    font-size: 13px;
    letter-spacing: 5px;
    color: var(--paper);
  }
</style>
</head>
<body>
<main class="sheet">
  <section class="card card-front" aria-label="Business card front">
    <div class="front-logo">Velk Partners Building</div>
    <div class="contact">
      <p class="name">Paul Osterby</p>
      <p class="role">CEO/Founder</p>
      <p>CSLB# 3867140</p>
      <p><span class="label">P :</span> (619) 555-0187</p>
      <p>paul@velkpartners.example</p>
      <p>www.velkpartners.example</p>
    </div>
    <svg class="emblem-area" viewBox="0 0 420 320" role="img" aria-label="Brand emblem artwork: large sun above ocean waves in gold and navy">
      <defs>
        <linearGradient id="emblemTone" x1="0" y1="0" x2="0" y2="1">
          <stop offset="0" stop-color="#ffffff"/>
          <stop offset="0.35" stop-color="#fbd66e"/>
          <stop offset="0.6" stop-color="#f5b324"/>
          <stop offset="0.75" stop-color="#1d3f80"/>
          <stop offset="1" stop-color="#17346b"/>
        </linearGradient>
      </defs>
      <rect width="420" height="320" fill="url(#emblemTone)"/>
    </svg>
  </section>

  <section class="card card-back" aria-label="Business card back">
    <div class="back-web">www.velkpartners.example</div>
    <div class="back-logo">Velk Partners Building</div>
  </section>
</main>
</body>
</html>
```